The Quiet Harbor Podcast Cover Art

I'm upgrading my podcast cover art to a new design. The show is called The Quiet Harbor and we interview guests who have gone through different challenges/adversities that we face in life. During the interview, we unpack how they've gotten past the adversity and how that insight might help others. I will link the show and old cover art. I will upload a new photo or two that can be used for the new cover art.

Look at previous cover for items that needed on the cover like Lyrabox, tunewell etc.

Should also have a small caption that states
“UNTOLD STORIES OF EVERYDAY ADVERSITY & PERSEVERANCE”

Tunewell: https://play.tunewellaudio.net/show/8PR4n2GbtqWxLoHvFNZCa7?si=qe3Lx8WbVm-D52KrPhtzRa

Target Market(s)

Podcast learning community

Industry/Entity Type

Podcast, Education

Colors
EB3D1F
EC4F4E
F09395
F8D3D4
FCEDEE

Requirements
Must have
• RM Logo, Colors are red, black and white.

```html
<!DOCTYPE html>
<html lang="en">
<head>
<meta charset="utf-8">
<title>The Quiet Harbor — Podcast Cover</title>
<link href="https://fonts.googleapis.com/css2?family=Montserrat:wght@400;500;700;800&display=swap" rel="stylesheet">
<style>
  :root {
    --wine: #6a1c22;
    --wine-deep: #4c1217;
    --red: #eb3d1f;
    --coral: #ec4f4e;
    --rose: #f09395;
    --blush: #f8d3d4;
    --mist: #fcedee;
    --white: #ffffff;
    --ink: #141414;
  }
  * { margin: 0; padding: 0; box-sizing: border-box; }
  html, body { width: 1200px; height: 1200px; overflow: hidden; background: var(--wine-deep); }
  .cover {
    position: relative;
    width: 1200px; height: 1200px;
    overflow: hidden;
    font-family: "Montserrat", sans-serif;
    color: var(--white);
    background:
      radial-gradient(ellipse 70% 60% at 50% 50%, var(--wine) 55%, rgba(106,28,34,0) 100%),
      radial-gradient(circle at 0% 0%, var(--coral) 0%, rgba(236,79,78,0) 35%),
      radial-gradient(circle at 100% 0%, var(--coral) 0%, rgba(236,79,78,0) 30%),
      radial-gradient(circle at 0% 100%, var(--red) 0%, rgba(235,61,31,0) 35%),
      radial-gradient(circle at 100% 100%, var(--coral) 0%, rgba(236,79,78,0) 35%),
      var(--wine);
  }
  .frame {
    position: absolute; inset: 16px;
    border: 3px solid rgba(248,211,212,0.55);
    pointer-events: none;
  }
  .decor, .host-photo { position: absolute; left: 0; top: 0; }
  .brand {
    position: absolute; top: 150px; left: 0; right: 0;
    text-align: center;
    display: flex; justify-content: center; align-items: center; gap: 18px;
  }
  .brand-mark {
    width: 28px; height: 28px;
    background: var(--white);
  }
  .brand-name {
    font-weight: 700; font-size: 60px; letter-spacing: 3px;
    text-transform: uppercase; line-height: 1;
  }
  .tagline {
    position: absolute; top: 322px; left: 0; right: 0;
    text-align: center; line-height: 1.18;
    text-transform: uppercase;
  }
  .tagline-strong { display: block; font-weight: 800; font-size: 53px; letter-spacing: 0.5px; }
  .tagline-light { display: block; font-weight: 400; font-size: 53px; letter-spacing: 1px; }
  .listing-badges {
    position: absolute; left: 56px; top: 1028px;
    display: flex; flex-direction: column; gap: 10px;
  }
  .listing-badge {
    width: 150px; height: 50px;
    border-radius: 8px;
    background: var(--ink);
    border: 2px solid rgba(255,255,255,0.35);
    display: flex; align-items: center; gap: 10px;
    padding: 0 10px;
    color: var(--white);
    font-weight: 700;
  }
  .badge-dot {
    width: 24px; height: 24px; border-radius: 50%;
    background: var(--white); flex: none;
  }
  .badge-text { display: flex; flex-direction: column; line-height: 1.05; }
  .badge-kicker { font-size: 10px; letter-spacing: 0.3px; }
  .badge-name { font-size: 19px; }
  .host-mark {
    position: absolute; right: 54px; top: 1012px;
    width: 150px; text-align: center;
  }
  .host-initials {
    font-weight: 500; font-size: 84px; letter-spacing: -4px; line-height: 1;
  }
  .host-name {
    margin-top: 8px;
    font-weight: 500; font-size: 15px; letter-spacing: 2px;
    text-transform: uppercase;
  }
</style>
</head>
<body>
<main class="cover">
  <svg class="decor" width="1200" height="1200" viewBox="0 0 1200 1200" aria-hidden="true">
    <circle cx="1145" cy="38" r="88" fill="var(--mist)" opacity="0.9"/>
    <circle cx="365" cy="560" r="66" fill="var(--blush)" opacity="0.85"/>
    <circle cx="0" cy="825" r="48" fill="var(--blush)" opacity="0.8"/>
  </svg>

  <svg class="host-photo" width="1200" height="1200" viewBox="0 0 1200 1200">
    <defs>
      <linearGradient id="photoTones" x1="0" y1="0" x2="0" y2="1">
        <stop offset="0" stop-color="#2b1b1c"/>
        <stop offset="0.4" stop-color="#6e6462"/>
        <stop offset="0.7" stop-color="#b5b0ae"/>
        <stop offset="1" stop-color="#1a1a1c"/>
      </linearGradient>
    </defs>
    <circle class="photo-ring" cx="600" cy="740" r="250" fill="var(--coral)"/>
    <g role="img" aria-label="Host photo: smiling man in a grey turtleneck wearing headphones, seated at a laptop with a studio microphone">
      <circle cx="600" cy="740" r="232" fill="url(#photoTones)"/>
      <rect x="300" y="900" width="600" height="300" rx="40" fill="url(#photoTones)"/>
    </g>
  </svg>

  <div class="frame"></div>

  <header class="brand">
    <span class="brand-mark"></span><span class="brand-name">The Quiet Harbor</span>
  </header>

  <h1 class="tagline">
    <span class="tagline-strong">Untold Stories of Everyday</span>
    <span class="tagline-light">Adversity &amp; Perseverance</span>
  </h1>

  <div class="listing-badges">
    <div class="listing-badge">
      <span class="badge-dot"></span>
      <span class="badge-text"><span class="badge-kicker">Listen On</span><span class="badge-name">Tunewell</span></span>
    </div>
    <div class="listing-badge">
      <span class="badge-dot"></span>
      <span class="badge-text"><span class="badge-kicker">Listen on</span><span class="badge-name">Lyrabox</span></span>
    </div>
  </div>

  <div class="host-mark">
    <div class="host-initials">RM</div>
    <div class="host-name">Ray Morrow</div>
  </div>
</main>
</body>
</html>
```